Rack Card Design Project

We are a locally family owned public golf course. We would like to have a rack card designed that can be used for multiple applications. The colors in our logo are grey, blue, and white. Please use those in the card design. The company logo, contact information, address, and summer pricing should be included. I've included some pictures that may or may not be used. I'm also open to suggestions....use one photo, multiple photos, a stock photo or image representing golf etc.

```html
<!DOCTYPE html>
<html lang="en">
<head>
<meta charset="utf-8">
<title>Summer Rates Rack Card</title>
<link href="https://fonts.googleapis.com/css2?family=Crimson+Text:wght@400;600;700&family=Playfair+Display:wght@500&display=swap" rel="stylesheet">
<style>
  :root{
    --navy:#1b3a6b;
    --blue:#2f5f9e;
    --row-light:#dbe9f7;
    --row-mid:#c4daf0;
    --grey:#9a9ea4;
    --grey-light:#d9dbde;
    --white:#ffffff;
    --ink:#222a35;
  }
  *{box-sizing:border-box;margin:0;padding:0}
  html,body{width:673px;height:1200px;overflow:hidden;background:#ececec}
  .rack-card{position:relative;width:673px;height:1200px;background:var(--white);overflow:hidden;font-family:"Crimson Text",serif}
  .hero-photo{position:absolute;left:0;top:0;width:673px;height:420px;
    background:linear-gradient(180deg,#5e8fa3 0%,#b7c4a8 38%,#e8c47a 55%,#7d8f4b 72%,#3f5f2c 100%)}
  .hero-frame{position:absolute;left:0;top:0}
  .club-badge{position:absolute;left:24px;top:24px;width:220px;height:220px;border-radius:50%;
    background:var(--navy);border:8px solid var(--grey-light);display:flex;align-items:center;justify-content:center;text-align:center;padding:26px}
  .club-badge span{font-family:"Crimson Text",serif;font-weight:700;color:var(--white);font-size:24px;line-height:1.15;letter-spacing:.5px}
  .course-photo{position:absolute;width:170px;height:170px;border-radius:50%;border:6px solid var(--white);box-shadow:0 2px 6px rgba(0,0,0,.25)}
  .course-photo.one{left:62px;top:300px;background:radial-gradient(circle at 50% 35%,#a9c9e6 0%,#6d9a4a 55%,#3e6a2a 100%)}
  .course-photo.two{left:252px;top:350px;background:radial-gradient(circle at 50% 30%,#c7dcef 0%,#8fb067 50%,#4e7a34 100%)}
  .course-photo.three{left:440px;top:294px;background:radial-gradient(circle at 50% 40%,#9cc0de 0%,#7aa85a 52%,#37622a 100%)}
  .rates{position:absolute;left:0;top:548px;width:673px;text-align:center}
  .rates-title{font-family:"Playfair Display",serif;font-weight:500;font-size:54px;color:var(--navy);line-height:1}
  .season-pill{display:inline-block;margin-top:12px;background:var(--navy);color:var(--white);font-size:30px;line-height:1.3;padding:2px 46px;border-radius:24px}
  .rate-table{margin:14px auto 0;width:450px;border-collapse:collapse;font-size:24px;color:var(--ink);text-align:left}
  .rate-table td{padding:2px 18px;height:36px}
  .rate-table tr:nth-child(odd){background:var(--row-light)}
  .rate-table tr:nth-child(even){background:var(--row-mid)}
  .rate-table .group td{font-weight:700;color:var(--navy)}
  .rate-table .price{text-align:right}
  .lunch-pill{display:inline-block;margin-top:14px;background:var(--navy);color:var(--white);font-size:22px;font-weight:600;line-height:1.3;padding:3px 36px;border-radius:20px}
  .contact{position:absolute;left:0;top:950px;width:673px;text-align:center;color:var(--ink)}
  .club-name{font-weight:700;font-size:24px;line-height:1.2;color:var(--navy)}
  .contact-line{display:flex;align-items:center;justify-content:center;gap:10px;margin-top:6px;font-size:22px;line-height:1.3}
  .contact-line.phone{font-size:28px;font-weight:600}
  .contact-line svg{width:24px;height:24px;flex:none}
  .footer-wave{position:absolute;left:0;bottom:0}
</style>
</head>
<body>
<main class="rack-card">
  <div class="hero-photo" role="img" aria-label="Golfer finishing a swing on a fairway at sunset"></div>
  <svg class="hero-frame" width="673" height="440" viewBox="0 0 673 440" aria-hidden="true">
    <path d="M0 360 C180 430 460 430 673 330 L673 440 L0 440 Z" fill="var(--white)"/>
    <path d="M0 345 C180 420 460 420 673 318 L673 334 C460 432 180 432 0 362 Z" fill="var(--navy)"/>
  </svg>
  <div class="club-badge"><span>The Links at Heron Bend Golf Club</span></div>

  <div class="course-photo one" role="img" aria-label="Clubhouse beside the course with palm trees"></div>
  <div class="course-photo two" role="img" aria-label="Tree-lined fairway under blue sky"></div>
  <div class="course-photo three" role="img" aria-label="Green and pond on the course"></div>

  <section class="rates">
    <h1 class="rates-title">Summer Rates</h1>
    <div class="season-pill">May 1 – September 30</div>
    <table class="rate-table">
      <tr class="group"><td colspan="2">18 Holes With Cart</td></tr>
      <tr><td>7AM – 11AM</td><td class="price">$24</td></tr>
      <tr><td>11AM – 3PM</td><td class="price">$19</td></tr>
      <tr><td>3PM – Close</td><td class="price">$15</td></tr>
      <tr class="group"><td>9 Holes With Cart</td><td class="price">$15</td></tr>
      <tr class="group"><td>Walking</td><td class="price">$12</td></tr>
    </table>
    <div class="lunch-pill">Lunch Available Daily : 10AM – 3PM</div>
  </section>

  <section class="contact">
    <div class="club-name">The Links at Heron Bend Golf Club</div>
    <div class="contact-line">
      <svg viewBox="0 0 24 24"><path d="M12 2a7 7 0 0 0-7 7c0 5 7 13 7 13s7-8 7-13a7 7 0 0 0-7-7zm0 9.5A2.5 2.5 0 1 1 12 6.5a2.5 2.5 0 0 1 0 5z" fill="var(--navy)"/></svg>
      1420 NW Cypress Hollow Rd, Harbor Town, FL 34000
    </div>
    <div class="contact-line phone">
      <svg viewBox="0 0 24 24"><circle cx="12" cy="12" r="12" fill="var(--navy)"/><path d="M9 6.5l1.6 3-1.2 1.2c.8 1.6 2.1 2.9 3.7 3.7l1.2-1.2 3 1.6-.6 2.3c-5.2.2-9.9-4.5-9.7-9.7z" fill="var(--white)"/></svg>
      555-014-2290
    </div>
    <div class="contact-line">
      <svg viewBox="0 0 24 24"><circle cx="12" cy="12" r="10" fill="none" stroke="var(--navy)" stroke-width="2"/><path d="M2 12h20M12 2c3 3 3 17 0 20M12 2c-3 3-3 17 0 20" fill="none" stroke="var(--navy)" stroke-width="1.6"/></svg>
      www.heronbendgolf.com
    </div>
  </section>

  <svg class="footer-wave" width="673" height="100" viewBox="0 0 673 100" aria-hidden="true">
    <path d="M0 40 C220 100 460 100 673 20 L673 100 L0 100 Z" fill="var(--grey)"/>
    <path d="M0 30 C220 88 460 88 673 8 L673 20 C460 100 220 100 0 40 Z" fill="var(--navy)"/>
  </svg>
</main>
</body>
</html>
```